House flipping business web site needed

pinecrestholdingsgroup.example.
I am a residential developer in Northern NJ and I am looking for a fresh new updated website. I have an intro video about my company being made now. I don't update it very often but I want an easy format that I can add update photos to on projects I have worked on or homes I renovate for sale.

Target Market(s)

investors into my projects so a portfolio , people looking to sell their homes to me.

Industry/Entity Type

Real Estate Development

Number of Pages Required

4 page

Font styles to use
Serif

Colors
33b8a4
39a9d7
cadf82

Requirements
Must have
• space for an intro video about my company
• a portfolio with pictures and information about each project
• Markets we serve- Morris County, NJ
• My logo- already created
• SEO
• Yes I would like this to function over all platforms. Phone, computer, all platforms.
• history and background page
• I am looking for a completed page that I can upload to the site that hosts my website
Nice to have
• I want something creative, easy to navigate. modern.

```html
<!DOCTYPE html>
<html lang="en">
<head>
<meta charset="utf-8">
<title>Pinecrest Holdings Group – House Flipping Business</title>
<link href="https://fonts.googleapis.com/css2?family=Oswald:wght@400&family=Roboto:wght@400;500&family=Roboto+Slab:wght@300;400&display=swap" rel="stylesheet">
<style>
:root{
  --teal:#33b8a4;
  --teal-dark:#2aa08f;
  --blue:#39a9d7;
  --blue-deep:#2f8fc4;
  --ink:#333333;
  --text:#555555;
  --muted:#888888;
  --footer:#2e2e2e;
  --rule:#e3e3e3;
  --white:#ffffff;
}
*{box-sizing:border-box;margin:0;padding:0}
html,body{width:1200px;height:2769px;overflow:hidden;background:var(--white)}
body{font-family:"Roboto Slab",Georgia,serif;color:var(--text);position:relative}
a{color:inherit;text-decoration:none}
ul{list-style:none}

/* Header */
.site-header{position:absolute;left:0;top:0;width:1200px;height:116px}
.brand{position:absolute;left:100px;top:30px;display:flex;align-items:center;gap:12px}
.brand-mark{width:40px;height:40px;border-radius:50%;background:var(--teal)}
.brand-name{font-family:"Roboto Slab",serif;font-size:22px;font-weight:400;color:var(--blue-deep);line-height:1.1;width:180px}
.follow{position:absolute;right:100px;top:20px;display:flex;align-items:center;gap:8px;font-family:"Roboto",sans-serif;font-size:12px;color:var(--muted)}
.follow span.sq{width:28px;height:28px;border-radius:3px;background:var(--blue)}
.follow span.sq:nth-child(odd){background:var(--teal)}
.main-nav{position:absolute;right:100px;top:66px;display:flex;gap:12px}
.main-nav a{display:block;height:36px;line-height:36px;padding:0 16px;font-family:"Roboto",sans-serif;font-size:13px;color:#777;text-transform:uppercase}
.main-nav a.active{background:var(--teal);color:var(--white)}

/* Hero */
.hero{position:absolute;left:0;top:116px;width:1200px;height:536px;background:linear-gradient(180deg,#6d7a86 0%,#4e5c68 45%,#3f5465 75%,#516677 100%)}
.hero-title{position:absolute;left:0;right:0;top:352px;text-align:center;font-family:"Oswald",sans-serif;font-size:60px;font-weight:400;color:var(--white);letter-spacing:-.5px}
.hero-dots{position:absolute;left:0;right:0;top:492px;display:flex;justify-content:center;gap:14px}
.hero-dots i{width:16px;height:16px;border:2px solid var(--white);border-radius:50%}

/* About */
.about{position:absolute;left:100px;top:690px;width:1000px}
.about-text{width:460px}
.section-title{font-family:"Roboto Slab",serif;font-weight:400;font-size:28px;color:var(--ink)}
.section-title em{font-style:normal;color:var(--teal)}
.about-text p{font-size:11.5px;line-height:20px;margin-top:14px;color:var(--text);text-align:justify}
.about-text .section-title{margin-bottom:6px}
.btn{display:inline-block;background:var(--teal);color:var(--white);font-family:"Roboto",sans-serif;font-size:11px;text-transform:uppercase;padding:0 14px;height:36px;line-height:36px}
.about-text .btn{margin-top:18px}
.video{position:absolute;left:502px;top:8px;width:498px;height:310px;border:4px solid var(--white);box-shadow:0 0 0 1px var(--rule);background:linear-gradient(180deg,#4a4236 0%,#3b4150 45%,#2f3a4e 100%)}
.video svg{position:absolute;left:216px;top:122px}

/* Services band */
.services{position:absolute;left:0;top:1062px;width:1200px;height:319px;background:linear-gradient(180deg,#4fb3dc 0%,#3a9fd0 100%);color:var(--white)}
.service{position:absolute;top:0;width:300px;margin-left:-150px;text-align:center}
.service:nth-child(1){left:244px}.service:nth-child(2){left:598px}.service:nth-child(3){left:952px}
.service-icon{margin:38px auto 0;width:140px;height:140px;border:2px solid rgba(255,255,255,.8);border-radius:50%;display:flex;align-items:center;justify-content:center}
.service-icon .inner{width:124px;height:124px;border:1px solid rgba(255,255,255,.5);border-radius:50%;display:flex;align-items:center;justify-content:center}
.service h3{margin-top:26px;font-family:"Roboto",sans-serif;font-weight:400;font-size:19px;text-transform:uppercase}
.service p{margin-top:10px;font-size:11px;line-height:20px}

/* Portfolio */
.portfolio{position:absolute;left:100px;top:1410px;width:1000px;text-align:center}
.section-sub{font-size:12.5px;color:var(--text);margin-top:4px}
.grid{display:grid;grid-template-columns:repeat(4,238px);gap:17px 16px;margin-top:26px}
.tile{height:171px;position:relative}
.t1{background:linear-gradient(180deg,#a8b3b8,#6c7b55 70%,#4d6433)}
.t2{background:linear-gradient(180deg,#c9c9c4,#9d9689 60%,#6f6858)}
.t3{background:linear-gradient(180deg,#3c4a4c,#2f3a3a 60%,#2a3220)}
.t4{background:linear-gradient(180deg,#a6a7a4,#9a7d60 60%,#7d5f44)}
.t5{background:linear-gradient(180deg,#3b6b9a,#2f5a86 50%,#8f3a3a)}
.t6{background:linear-gradient(180deg,#a08256,#8b6e48 60%,#b59a6f)}
.t7{background:linear-gradient(180deg,#cfd3d5,#a3a293 55%,#7d7a62)}
.t8{background:linear-gradient(180deg,#4d453e,#6b5f52 60%,#8a7b69)}
.tile-actions{position:absolute;left:0;right:0;top:86px;display:flex;justify-content:center;gap:24px}
.tile-actions span{width:32px;height:32px;border-radius:50%;background:#3ad68f;display:flex;align-items:center;justify-content:center}

/* Blog */
.blog{position:absolute;left:100px;top:1900px;width:1000px;text-align:center}
.blog .intro{width:740px;margin:10px auto 0;font-size:12.5px;line-height:22px;color:var(--text)}
.posts{display:grid;grid-template-columns:repeat(3,325px);gap:13px;margin-top:22px;text-align:left}
.post-img{height:180px}
.p1{background:linear-gradient(180deg,#1f3c86,#2d56b0 55%,#0f1f44)}
.p2{background:linear-gradient(180deg,#7eb0e6,#c7a57b 55%,#8f6c5a)}
.p3{background:linear-gradient(180deg,#5f97d8,#a7bdd4 55%,#6f8a55)}
.post h4{margin-top:20px;font-family:"Roboto",sans-serif;font-weight:400;font-size:17px;color:var(--ink);text-transform:uppercase}
.meta{margin-top:6px;font-family:"Roboto",sans-serif;font-size:11px;color:var(--blue);display:flex;align-items:center;gap:6px}
.meta .sep{color:var(--muted);margin:0 6px}
.post p{margin-top:8px;font-size:11.5px;line-height:20px;color:var(--text)}
.post .more{display:block;margin-top:6px;font-family:"Roboto",sans-serif;font-size:11px;color:var(--blue);text-transform:uppercase}

/* Footer */
.site-footer{position:absolute;left:0;top:2372px;width:1200px;height:333px;background:var(--footer);color:#ddd}
.newsletter{position:absolute;left:100px;top:33px;width:1000px;height:42px;display:flex;align-items:center}
.newsletter h3{font-family:"Roboto",sans-serif;font-weight:400;font-size:22px;color:var(--white);text-transform:uppercase;width:330px}
.newsletter .field{width:508px;height:42px;background:var(--white);border-radius:3px;font-family:"Roboto",sans-serif;font-size:11px;color:#777;line-height:42px;padding-left:16px}
.newsletter .btn{margin-left:8px;width:157px;height:42px;line-height:42px;text-align:center;border-radius:3px}
.foot-col{position:absolute;top:124px}
.foot-col h4{font-family:"Roboto",sans-serif;font-weight:400;font-size:15px;color:var(--white);text-transform:uppercase}
.foot-col ul{margin-top:28px}
.foot-col li{font-family:"Roboto",sans-serif;font-size:11.5px;height:27px;display:flex;align-items:center;gap:18px}
.foot-col li::before{content:"";border-left:5px solid #ddd;border-top:4px solid transparent;border-bottom:4px solid transparent}
.c-info{left:100px}.c-contact{left:397px;width:230px}.c-links{left:681px}.c-follow{left:895px;width:210px}
.contact-row{margin-top:28px;display:flex;gap:14px;font-family:"Roboto",sans-serif;font-size:11.5px;line-height:16px}
.contact-row svg{flex:none;margin-top:2px}
.c-follow p{margin-top:28px;font-family:"Roboto",sans-serif;font-size:11.5px;line-height:18px}
.socials{margin-top:16px;display:flex;gap:9px}
.socials i{width:36px;height:36px;border:1.5px solid #ddd;border-radius:50%}
.copyright{position:absolute;left:0;top:2705px;width:1200px;height:64px;background:linear-gradient(180deg,#4fb3dc,#3a9fd0);color:var(--white);font-family:"Roboto",sans-serif;font-size:11px;text-align:center;line-height:64px}
</style>
</head>
<body>

<header class="site-header">
  <a class="brand" href="#"><span class="brand-mark"></span><span class="brand-name">Pinecrest Holdings Group</span></a>
  <div class="follow">Follow US :<span class="sq"></span><span class="sq"></span><span class="sq"></span><span class="sq"></span></div>
  <nav class="main-nav">
    <a class="active" href="#">Home</a><a href="#">About</a><a href="#">Contact</a><a href="#">Portfolio</a><a href="#">Contact Us</a>
  </nav>
</header>

<section class="hero" role="img" aria-label="City skyline across the river at dusk">
  <h1 class="hero-title">HOUSE FLIPPING BUSINESS</h1>
  <div class="hero-dots"><i></i><i></i><i></i></div>
</section>

<section class="about">
  <div class="about-text">
    <h2 class="section-title">About Pinecrest Holdings <em>Group</em></h2>
    <p>Pinecrest Holdings Group is a family run business with 3rd generation builders and renovators in the Morris County area. As the President and owner of Pinecrest Holdings Group I am dedicated to working hard to create opportunities for investment through real estate. At Pinecrest Holdings Group we have a valuable support system and a team of investors, realtors, attorneys, contractors and property managers providing a combined package offering years of experience in the local market.</p>
    <p>We are a team of experienced home buyers and renovators in the Morris County, NJ area. Our specialty is purchasing distressed homes and property. We then collaborate with the best talents in Northern New Jersey to renovate those properties and transform them into the best house in the neighborhood.</p>
    <a class="btn" href="#">Learn More</a>
  </div>
  <div class="video" role="img" aria-label="Intro video still: family seated by a lake in autumn">
    <svg width="66" height="66" viewBox="0 0 66 66"><circle cx="33" cy="33" r="31" fill="none" stroke="#fff" stroke-width="2.5"/><path d="M26 20 L47 33 L26 46 Z" fill="#fff"/></svg>
  </div>
</section>

<section class="services">
  <div class="service">
    <div class="service-icon"><div class="inner">
      <svg width="56" height="56" viewBox="0 0 56 56" fill="none" stroke="#fff" stroke-width="3"><rect x="6" y="14" width="34" height="24" rx="2"/><path d="M18 46h10M23 38v8"/><circle cx="42" cy="14" r="7"/><circle cx="42" cy="14" r="2.5" fill="#fff"/></svg>
    </div></div>
    <h3>Neighborhood</h3>
    <p>We only buy and renovate homes in our neighborhoods<br>right here in the Morris County, NJ area.</p>
  </div>
  <div class="service">
    <div class="service-icon"><div class="inner">
      <svg width="60" height="56" viewBox="0 0 60 56" fill="#fff"><path d="M4 20l12-6 14 8 14-8 12 6v14l-8 4-14 10c-2 1-4 1-5-1L14 38 4 34z"/></svg>
    </div></div>
    <h3>How We Can Help</h3>
    <p>Do you need to sell your home fast to avoid foreclosure,<br>have estate home you do not want to fix to put</p>
  </div>
  <div class="service">
    <div class="service-icon"><div class="inner">
      <svg width="50" height="60" viewBox="0 0 50 60" fill="none" stroke="#fff" stroke-width="3" stroke-linejoin="round"><path d="M16 34V8a4 4 0 0 1 8 0v18l14 3c4 1 6 4 5 8l-3 15H18L8 38a4 4 0 0 1 6-5z"/></svg>
    </div></div>
    <h3>Financing</h3>
    <p>We only buy and renovate homes in our neighborhoods<br>right here in the Morris County, NJ area.</p>
  </div>
</section>

<section class="portfolio">
  <h2 class="section-title">Our <em>Portfolio</em></h2>
  <p class="section-sub">We bring excellence to the home buying and renovation business.</p>
  <div class="grid">
    <div class="tile t1" role="img" aria-label="Renovated two-story house with lawn"></div>
    <div class="tile t2" role="img" aria-label="Grey house with stone garden wall"></div>
    <div class="tile t3" role="img" aria-label="Dark-sided house exterior">
      <div class="tile-actions">
        <span><svg width="16" height="10" viewBox="0 0 16 10"><path d="M1 5c3-5 11-5 14 0-3 5-11 5-14 0z" fill="#1e7a55"/><circle cx="8" cy="5" r="2" fill="#3ad68f"/></svg></span>
        <span><svg width="14" height="14" viewBox="0 0 14 14" fill="none" stroke="#1e7a55" stroke-width="2"><path d="M6 8l2-2M5 5L3 7a2 2 0 0 0 3 3l1-1M9 9l2-2a2 2 0 0 0-3-3L7 5"/></svg></span>
      </div>
    </div>
    <div class="tile t4" role="img" aria-label="Porch under construction"></div>
    <div class="tile t5" role="img" aria-label="Radiant floor heating tubes being installed"></div>
    <div class="tile t6" role="img" aria-label="Unfinished basement with framing"></div>
    <div class="tile t7" role="img" aria-label="White house above a stone retaining wall"></div>
    <div class="tile t8" role="img" aria-label="Finished living room with fireplace"></div>
  </div>
</section>

<section class="blog">
  <h2 class="section-title">Our <em>Blog</em></h2>
  <p class="intro">We only work in the Morris County area so we are local and know the area and market. We can finance or buy your home for cash. Our team will do any major renovations to the home or property and then make</p>
  <div class="posts">
    <article class="post">
      <div class="post-img p1" role="img" aria-label="City skyline at night over water"></div>
      <h4>Our Blog Text</h4>
      <div class="meta"><span>&#9638; Agu 22, 2016</span><span class="sep">|</span><span>&#9993; 2 Comments</span></div>
      <p>There are many variations passages of Lorem Ipsum available, but the majority have suffered alteration.</p>
      <a class="more" href="#">Learn More</a>
    </article>
    <article class="post">
      <div class="post-img p2" role="img" aria-label="Boardwalk with colorful buildings"></div>
      <h4>Our Blog Text</h4>
      <div class="meta"><span>&#9638; Agu 22, 2016</span><span class="sep">|</span><span>&#9993; 2 Comments</span></div>
      <p>There are many variations passages of Lorem Ipsum available, but the majority have suffered alteration.</p>
      <a class="more" href="#">Learn More</a>
    </article>
    <article class="post">
      <div class="post-img p3" role="img" aria-label="Downtown towers under blue sky"></div>
      <h4>Our Blog Text</h4>
      <div class="meta"><span>&#9638; Agu 22, 2016</span><span class="sep">|</span><span>&#9993; 2 Comments</span></div>
      <p>There are many variations passages of Lorem Ipsum available, but the majority have suffered alteration.</p>
      <a class="more" href="#">Learn More</a>
    </article>
  </div>
</section>

<footer class="site-footer">
  <div class="newsletter">
    <h3>Subscribe Newsletter :</h3>
    <div class="field">Enter Your Email id:</div>
    <a class="btn" href="#">Subscribe Now</a>
  </div>
  <div class="foot-col c-info">
    <h4>Information</h4>
    <ul><li>About Us</li><li>Who We Are?</li><li>Our Farms</li><li>How To Order?</li><li>Contact Us</li></ul>
  </div>
  <div class="foot-col c-contact">
    <h4>Contact Us</h4>
    <div class="contact-row">
      <svg width="10" height="14" viewBox="0 0 10 14"><path d="M5 0a5 5 0 0 1 5 5c0 4-5 9-5 9S0 9 0 5a5 5 0 0 1 5-5z" fill="#ddd"/><circle cx="5" cy="5" r="1.8" fill="#2e2e2e"/></svg>
      <span>Denouncing pleasure and praising pain was born and I will give you a complete account of the system, and expound the actual teachings of the great</span>
    </div>
    <div class="contact-row">
      <svg width="14" height="12" viewBox="0 0 14 12"><path d="M1 3c0-2 12-2 12 0v2H10V3H4v2H1zM3 6h8l2 5H1z" fill="#ddd"/></svg>
      <span>(000) 555.010.2044 (Phone)</span>
    </div>
  </div>
  <div class="foot-col c-links">
    <h4>Quick Links</h4>
    <ul><li>Good Directory</li><li>Diary</li><li>news stories</li><li>About</li><li>Contact Us</li></ul>
  </div>
  <div class="foot-col c-follow">
    <h4>Follow Us</h4>
    <p>Perspiciatis unde omnis iste natus oluptatem accusantium beatae vitae dicta sunt explicabo.</p>
    <div class="socials"><i></i><i></i><i></i><i></i><i></i></div>
  </div>
</footer>
<div class="copyright">© Copyright 2016. pinecrestholdingsgroup.example. All Rights Reserved.</div>

</body>
</html>
```